VeraMosk Powerpoint design

We've recently redesigned our logos and would like a single presentation format that we can easily interchange the logos attached into. The presentation will be used for general company sales information. The group is called VeraMosk and has 2 companies, k7datagrove and Copper Thread. We're an IT services company who specialises in Broadband and general network services.

Target Market(s)

Professional

```html
<!DOCTYPE html>
<html lang="en">
<head>
<meta charset="utf-8">
<title>VeraMosk Presentation Template</title>
<link href="https://fonts.googleapis.com/css2?family=Roboto:wght@300;400;500;700;900&display=swap" rel="stylesheet">
<style>
:root{
  --navy:#1d2d8a;
  --blue:#1f6fc4;
  --sky:#2e9ee0;
  --red:#d21033;
  --ink:#262626;
  --grey:#7a7a7a;
  --paper:#ffffff;
  --line:#e3e3e3;
}
*{margin:0;padding:0;box-sizing:border-box}
html,body{width:1200px;height:1200px;overflow:hidden;background:var(--paper)}
body{position:relative;font-family:'Roboto',Arial,sans-serif;color:var(--ink)}
.slide{position:absolute;width:271px;height:153px;overflow:hidden;background:var(--paper);box-shadow:0 3px 9px rgba(0,0,0,.2)}
.abs{position:absolute}
.brand{position:absolute;top:8px;left:11px;font:700 6px 'Roboto',sans-serif;color:var(--ink);display:flex;align-items:center;gap:2px}
.brand::before{content:"";width:5px;height:5px;border-radius:50%;background:var(--blue)}
.brand.right{left:auto;right:11px}
.brand.light{color:#fff}
.brand.light::before{background:#fff}
.pnum{position:absolute;left:0;bottom:0;width:6px;height:6px;background:var(--red)}
.foot{position:absolute;bottom:5px;font-size:2.6px;color:#aaa;width:100%;text-align:center}
.title{font-size:13px;line-height:1.15;color:var(--ink);font-weight:300;white-space:nowrap}
.title b{font-weight:700}
.title.light{color:#fff}
.dots{display:flex;gap:1.5px;margin:3px 0}
.dots i{width:2.6px;height:2.6px;border-radius:50%;background:var(--navy)}
.sub{font-size:3.6px;font-weight:700;margin-bottom:2px}
.p{font-size:3.1px;line-height:4.6px;color:var(--grey);text-align:justify}
.p.c{text-align:center}
.p.r{text-align:right}
.light-text{color:#fff}
.photo{position:absolute}
.ph-server{background:linear-gradient(135deg,#2d3b56,#c9a43a 45%,#3a6ea8 70%,#1b2436)}
.ph-fiber{background:radial-gradient(circle at 30% 40%,#9fe4ff,#1a7fb5 35%,#06223a 80%)}
.ph-purple{background:linear-gradient(160deg,#3b1a8a,#8a3fd0 45%,#e05ad8 70%,#1a2a7a)}
.ph-red{background:linear-gradient(160deg,#1a0a2e,#b1123a 55%,#3a1a7a)}
.ph-keys{background:linear-gradient(140deg,#6a7480,#cfd4d8 45%,#3a8eaa 80%)}
.mark{position:absolute;border-radius:50%;display:flex;align-items:center;justify-content:center;font-weight:700;color:var(--ink);background:#fff;box-shadow:0 1px 3px rgba(0,0,0,.2)}
.icon{position:absolute;border-radius:50%;background:var(--navy);display:flex;align-items:center;justify-content:center;box-shadow:0 0 0 2px #dfe6f5}
.icon svg{width:55%;height:55%}
.item .h{font-size:3.5px;font-weight:700}
.item .p{font-size:2.9px;line-height:3.8px}
</style>
</head>
<body>
<svg width="0" height="0" style="position:absolute">
  <defs>
    <symbol id="i-server" viewBox="0 0 24 24"><g fill="none" stroke="#fff" stroke-width="2"><rect x="4" y="3" width="16" height="5"/><rect x="4" y="10" width="16" height="5"/><path d="M12 15v4M6 20h12"/></g></symbol>
    <symbol id="i-monitor" viewBox="0 0 24 24"><g fill="none" stroke="#fff" stroke-width="2"><rect x="3" y="4" width="18" height="12" rx="1"/><path d="M9 20h6M12 16v4"/></g></symbol>
    <symbol id="i-usb" viewBox="0 0 24 24"><g fill="none" stroke="#fff" stroke-width="2"><path d="M12 2v20M12 6l-4 4v3M12 9l4 3v2"/><circle cx="12" cy="20" r="2"/></g></symbol>
    <symbol id="i-net" viewBox="0 0 24 24"><g fill="none" stroke="#fff" stroke-width="2"><circle cx="12" cy="12" r="2.5"/><path d="M12 3v6.5M12 14.5V21M3 12h6.5M14.5 12H21M5.5 5.5l4.7 4.7M13.8 13.8l4.7 4.7"/></g></symbol>
    <symbol id="i-cloud" viewBox="0 0 24 24"><g fill="none" stroke="#fff" stroke-width="2"><path d="M7 18h10a4 4 0 0 0 0-8 6 6 0 0 0-11.5 1.5A3.3 3.3 0 0 0 7 18z"/><path d="M12 10v6M9.5 13.5 12 16l2.5-2.5"/></g></symbol>
    <symbol id="i-plug" viewBox="0 0 24 24"><g fill="none" stroke="#fff" stroke-width="2"><rect x="5" y="6" width="5" height="10" rx="1"/><rect x="14" y="6" width="5" height="10" rx="1"/><path d="M7.5 16v5M16.5 16v5M7.5 3v3M16.5 3v3"/></g></symbol>
  </defs>
</svg>

<!-- Row 1 -->
<section class="slide" style="left:22px;top:61px;background:linear-gradient(120deg,#1a8ec0,#128a5c 45%,#0b5e3a)">
  <div class="mark" style="left:18px;top:25px;width:100px;height:100px;background:#161a2a;color:#fff;font-size:10px">VeraMosk</div>
  <div class="abs" style="left:150px;top:40px">
    <div class="title light"><b>Your Title<br>Presentation</b><br>Right Here</div>
    <div class="p light-text" style="margin-top:3px;font-size:4.4px;line-height:6px;text-align:left">Your Subtitle Slide Goes Right Here<br>Presented by : Alan Pryce<br>Date May, 23, 2023</div>
  </div>
  <div class="foot" style="color:#dfe">© 2023 VeraMosk group all rights reserved</div>
</section>

<section class="slide" style="left:317px;top:61px;background:linear-gradient(120deg,#c9112a,#9a2a22 40%,#3a8a3a 75%,#1a8ab8)">
  <div class="mark" style="left:18px;top:25px;width:100px;height:100px;background:#161a2a;color:#fff;font-size:10px">VeraMosk</div>
  <div class="abs" style="left:144px;top:39px">
    <div class="title light"><b>Your Title<br>Presentation</b><br>Right Here</div>
    <div class="p light-text" style="margin-top:3px;font-size:4.4px;line-height:6px;text-align:left">Your Subtitle Slide Goes Right Here<br>Presented by : Alan Pryce<br>Date May, 23, 2023</div>
  </div>
  <div class="foot" style="color:#fdd">© 2023 VeraMosk group all rights reserved</div>
</section>

<section class="slide" style="left:612px;top:61px">
  <div class="brand">VeraMosk</div><div class="brand right">Copper Thread</div>
  <div class="photo ph-server" role="img" aria-label="Network engineer in a server room" style="left:164px;top:21px;width:107px;height:132px"></div>
  <div class="abs" style="left:28px;top:30px;width:125px">
    <div class="title"><b>Your Title</b> Slide</div>
    <div class="dots"><i></i><i></i><i></i></div>
    <div class="sub">Your Subtitle Slide Goes Right Here</div>
    <div class="p">Lorem Ipsum is simply dummy text of the printing and typesetting industry. Lorem Ipsum has been the industry's standard dummy text ever since the 1500s, when an unknown printer took a galley of type and scrambled it to make a type specimen book. It has survived not only five centuries, but also the leap into electronic typesetting, remaining essentially unchanged.</div>
  </div>
  <div class="abs" style="left:150px;top:100px;width:108px;height:32px;background:#fff;padding:3px 4px 0 30px">
    <div class="item"><div class="h" style="text-align:right">Your Subtitle Slide Goes Right Here</div><div class="p r">Lorem Ipsum is simply dummy text of the printing and typesetting industry.</div></div>
  </div>
  <div class="mark" style="left:147px;top:103px;width:26px;height:26px;font-size:3.6px;box-shadow:0 0 0 2px #eaeaea">VeraMosk</div>
  <div class="pnum"></div>
</section>

<section class="slide" style="left:906px;top:61px">
  <div class="brand">VeraMosk</div><div class="brand right">Copper Thread</div>
  <div class="photo ph-server" role="img" aria-label="Technician checking server cabling" style="left:0;top:21px;width:108px;height:132px"></div>
  <div class="abs" style="left:0;top:100px;width:120px;height:32px;background:#fff;padding:3px 30px 0 12px">
    <div class="item"><div class="h">Your Subtitle Slide Goes Right Here</div><div class="p" style="text-align:left">Lorem Ipsum is simply dummy text of the printing industry.</div></div>
  </div>
  <div class="mark" style="left:95px;top:103px;width:26px;height:26px;font-size:3.6px;box-shadow:0 0 0 2px #eaeaea">VeraMosk</div>
  <div class="abs" style="left:152px;top:30px;width:100px">
    <div class="title"><b>Your Title</b> Slide</div>
    <div class="dots"><i></i><i></i><i></i></div>
    <div class="sub">Your Subtitle Slide Goes Right Here</div>
    <div class="p">Lorem Ipsum is simply dummy text of the printing and typesetting industry. Lorem Ipsum has been the industry's standard dummy text ever since the 1500s, when an unknown printer took a galley of type and scrambled it to make a type specimen book. It has survived not only five centuries.</div>
  </div>
</section>

<!-- Row 2 -->
<section class="slide" style="left:22px;top:246px;background:linear-gradient(110deg,#1e7a3e,#2e8f4e 55%,#17552e)">
  <div class="photo" role="img" aria-label="Engineer standing in a data centre" style="left:100px;top:0;width:171px;height:153px;background:linear-gradient(90deg,rgba(255,255,255,.05),rgba(200,230,200,.18),rgba(0,40,20,.1))"></div>
  <div class="brand light">VeraMosk</div><div class="brand right light">Copper Thread</div>
  <div class="mark" style="left:30px;top:30px;width:90px;height:90px;background:#eef2ef;font-size:9px;box-shadow:0 0 0 3px rgba(255,255,255,.4)">VeraMosk</div>
  <div class="abs" style="right:12px;top:33px;width:110px;text-align:right">
    <div class="title light" style="text-align:right"><b>ABOUT</b><br><b>VeraMosk</b> Group</div>
    <div class="p r light-text" style="margin-top:3px">Lorem Ipsum is simply dummy text of the printing and typesetting industry. Lorem Ipsum has been the industry's standard dummy text ever since the 1500s, when an unknown printer took a galley of type and scrambled it to make a type specimen book. It has survived not only five centuries, but also the leap into electronic typesetting, remaining essentially unchanged.</div>
  </div>
  <div class="foot" style="color:#cfe">© 2023 VeraMosk group all rights reserved</div>
</section>

<section class="slide" style="left:317px;top:246px">
  <div class="brand">VeraMosk</div><div class="brand right">Copper Thread</div>
  <div class="abs" style="left:28px;top:30px;width:112px">
    <div class="title"><b>Your Title</b> Slide</div>
    <div class="dots"><i></i><i></i><i></i></div>
    <div class="sub">Your Subtitle Slide Goes Right Here</div>
    <div class="p">Lorem Ipsum is simply dummy text of the printing and typesetting industry. Lorem Ipsum has been the industry's standard dummy text ever since the 1500s, when an unknown printer took a galley of type and scrambled it to make a type specimen book. It has survived not only five centuries, but also the leap into electronic typesetting, remaining essentially unchanged.</div>
  </div>
  <div class="mark" style="left:163px;top:30px;width:95px;height:95px;background:linear-gradient(135deg,#2c8ab8,#1e6a4a 50%,#b8203a);color:#fff;font-size:9px">VeraMosk</div>
  <div class="foot">© 2023 VeraMosk group all rights reserved</div>
  <div class="pnum"></div>
</section>

<section class="slide" style="left:612px;top:246px">
  <div class="brand">VeraMosk</div><div class="brand right">Copper Thread</div>
  <div class="abs" style="left:0;top:22px;width:271px;text-align:center">
    <div class="title"><b>Your Title</b> Slide</div>
    <div class="p c" style="padding:3px 28px 0">Lorem Ipsum is simply dummy text of the printing and typesetting industry. Lorem Ipsum has been the industry's standard dummy text ever since the 1500s, when an unknown printer took a galley of type and scrambled it to make a type.</div>
  </div>
  <div class="photo ph-purple" role="img" aria-label="Glowing fibre optic strands" style="left:0;top:83px;width:271px;height:70px"></div>
  <div class="abs" style="left:59px;top:70px;display:flex;gap:5px">
    <div style="width:48px;height:57px;background:#fff;box-shadow:0 1px 3px rgba(0,0,0,.2)"><div style="height:22px;background:var(--navy);display:flex;align-items:center;justify-content:center"><svg width="12" height="12"><use href="#i-plug"/></svg></div><div class="p c" style="color:#333;font-weight:700;margin-top:3px;font-size:3.3px">Vector Based</div><div class="p c" style="font-size:2.6px;line-height:3.6px">Ipsum volutpat tincidunt dapibus integer iste</div></div>
    <div style="width:48px;height:57px;background:#fff;box-shadow:0 1px 3px rgba(0,0,0,.2)"><div style="height:22px;background:var(--blue);display:flex;align-items:center;justify-content:center"><svg width="12" height="12"><use href="#i-monitor"/></svg></div><div class="p c" style="color:#333;font-weight:700;margin-top:3px;font-size:3.3px">Fine Layout</div><div class="p c" style="font-size:2.6px;line-height:3.6px">Ipsum volutpat tincidunt dapibus integer iste</div></div>
    <div style="width:48px;height:57px;background:#fff;box-shadow:0 1px 3px rgba(0,0,0,.2)"><div style="height:22px;background:var(--navy);display:flex;align-items:center;justify-content:center"><svg width="12" height="12"><use href="#i-usb"/></svg></div><div class="p c" style="color:#333;font-weight:700;margin-top:3px;font-size:3.3px">Placeholder</div><div class="p c" style="font-size:2.6px;line-height:3.6px">Ipsum volutpat tincidunt dapibus integer iste</div></div>
  </div>
  <div class="pnum"></div>
</section>

<section class="slide" style="left:906px;top:246px">
  <div class="photo ph-server" role="img" aria-label="Server rack with network cables" style="left:0;top:0;width:271px;height:153px"></div>
  <div class="abs" style="left:16px;top:15px;width:240px;height:122px;background:rgba(255,255,255,.88)"></div>
  <div class="mark" style="left:214px;top:22px;width:24px;height:24px;font-size:3.4px">VeraMosk</div>
  <div class="abs" role="img" aria-label="Desk with computer and office items" style="left:28px;top:75px;width:55px;height:40px;background:linear-gradient(135deg,#e4e6ea,#b9c0c8)"></div>
  <div class="abs" style="left:50px;top:56px;width:196px;text-align:right">
    <div style="font-size:6px;line-height:7.6px;color:#222"><b>Lorem Ipsum is simply</b> dummy text of the printing <b>and typesetting industry. Lorem Ipsum</b> has been the industry's <b>standard dummy text ever since the 1500s, when an</b></div>
    <div class="p r" style="margin-top:3px;padding-left:50px">Lorem Ipsum is simply dummy text of the printing and typesetting industry. Lorem Ipsum has been the industry's standard dummy text ever since the 1500s, when an unknown printer took a galley of type and scrambled it to make a type specimen book. It has survived not only five centuries, but also the leap into electronic typesetting, remaining essentially</div>
  </div>
  <div class="pnum"></div>
</section>

<!-- Row 3 -->
<section class="slide" style="left:22px;top:431px">
  <div class="brand right">Copper Thread</div>
  <div class="photo ph-keys" role="img" aria-label="Network cable plugged in beside a keyboard" style="left:10px;top:10px;width:86px;height:131px"></div>
  <div class="mark" style="left:84px;top:26px;width:24px;height:24px;font-size:3.4px">VeraMosk</div>
  <div class="abs" style="left:120px;top:26px;width:130px">
    <div class="title"><b>Your Title Slide</b><br>Goes Right Here</div>
    <div class="p" style="margin-top:4px">Lorem Ipsum is simply dummy text of the printing and typesetting industry. Lorem Ipsum has been the industry's standard dummy text ever since the 1500s, when an unknown printer took a galley of type and scrambled it to make a type specimen book. It has survived not only five centuries, but also the leap into electronic typesetting, remaining essentially</div>
  </div>
  <div class="icon" style="left:121px;top:109px;width:14px;height:14px"><svg><use href="#i-server"/></svg></div>
  <div class="icon" style="left:139px;top:109px;width:14px;height:14px;background:var(--blue)"><svg><use href="#i-cloud"/></svg></div>
  <div class="icon" style="left:157px;top:109px;width:14px;height:14px;background:var(--sky)"><svg><use href="#i-net"/></svg></div>
  <div class="item abs" style="left:180px;top:108px;width:75px"><div class="h">Your Subtitle Slide Right Here</div><div class="p" style="text-align:left">Lorem Ipsum is simply dummy text of the printing and typesetting industry.</div></div>
  <div class="foot">© 2023 VeraMosk group all rights reserved</div>
  <div class="pnum"></div>
</section>

<section class="slide" style="left:317px;top:431px">
  <div class="brand">VeraMosk</div><div class="brand right">Copper Thread</div>
  <div class="abs" style="left:24px;top:35px;width:118px">
    <div class="title"><b>Your Title Slide</b><br>Goes Right Here</div>
    <div class="p" style="margin-top:4px">Lorem Ipsum is simply dummy text of the printing and typesetting industry. Lorem Ipsum has been the industry's standard dummy text ever since the 1500s, when an unknown printer took a galley of type and scrambled it to make a type</div>
  </div>
  <svg class="abs" style="left:26px;top:109px" width="16" height="16" viewBox="0 0 24 24"><g fill="none" stroke="#1e7a3e" stroke-width="1.8"><rect x="4" y="3" width="12" height="14" rx="1"/><path d="M8 17v4h8M14 10l4 4"/></g></svg>
  <div class="item abs" style="left:54px;top:112px;width:75px"><div class="h">Your Subtitle Slide Right Here</div><div class="p" style="text-align:left">Lorem Ipsum is simply dummy text of the printing and typesetting industry.</div></div>
  <div class="icon" style="left:155px;top:37px;width:17px;height:17px"><svg><use href="#i-usb"/></svg></div>
  <div class="item abs" style="left:180px;top:36px;width:75px"><div class="h">Your Subtitle Slide Right Here</div><div class="p">Lorem Ipsum is simply dummy text of the printing and typesetting industry. Lorem Ipsum has been the industry's</div></div>
  <div class="icon" style="left:155px;top:71px;width:17px;height:17px"><svg><use href="#i-monitor"/></svg></div>
  <div class="item abs" style="left:180px;top:70px;width:75px"><div class="h">Your Subtitle Slide Right Here</div><div class="p">Lorem Ipsum is simply dummy text of the printing and typesetting industry. Lorem Ipsum has been the industry's</div></div>
  <div class="icon" style="left:155px;top:106px;width:17px;height:17px;background:var(--blue)"><svg><use href="#i-plug"/></svg></div>
  <div class="item abs" style="left:180px;top:105px;width:75px"><div class="h">Your Subtitle Slide Right Here</div><div class="p">Lorem Ipsum is simply dummy text of the printing and typesetting industry. Lorem Ipsum has been the industry's</div></div>
  <div class="foot">© 2023 VeraMosk group all rights reserved</div>
  <div class="pnum"></div>
</section>

<section class="slide" style="left:612px;top:431px">
  <div class="brand">VeraMosk</div><div class="brand right">Copper Thread</div>
  <div class="mark" style="left:18px;top:30px;width:100px;height:100px;background:linear-gradient(135deg,#2c8ab8,#1e6a4a 50%,#b8203a);color:#fff;font-size:10px">VeraMosk</div>
  <div class="abs" style="right:12px;top:30px;width:118px;text-align:right">
    <div class="title" style="text-align:right"><b>Your Title Slide</b><br>Goes Right Here</div>
    <div class="p r" style="margin-top:4px;color:#333;font-weight:700;font-size:3.4px">Lorem Ipsum is simply dummy text of the printing and typesetting industry. Lorem Ipsum has been the industry's</div>
    <div class="p r" style="margin-top:2px">Lorem Ipsum is simply dummy text of the printing and typesetting industry. Lorem Ipsum has been the industry's standard dummy text ever since the 1500s, when an unknown printer took a galley of type and scrambled it to make a type specimen book. It has survived not only five centuries, but also the leap into electronic typesetting, remaining essentially</div>
  </div>
  <div class="foot">© 2023 VeraMosk group all rights reserved</div>
  <div class="pnum"></div>
</section>

<section class="slide" style="left:906px;top:431px">
  <div class="brand">VeraMosk</div><div class="brand right">Copper Thread</div>
  <div class="abs" style="left:28px;top:30px;width:115px">
    <div class="title"><b>Creative</b> Timeline</div>
    <div class="dots"><i></i><i></i><i></i></div>
    <div class="sub">Your Subtitle Slide Goes Right Here</div>
    <div class="p">Lorem Ipsum is simply dummy text of the printing and typesetting industry. Lorem Ipsum has been the industry's standard dummy text ever since the 1500s, when an unknown printer took a galley of type and scrambled it to make a type specimen book. It has survived not only five centuries, but also the leap into electronic typesetting, remaining essentially unchanged. It was popularized in the 1960s with the release of transfer sheets containing Lorem Ipsum passages, and more</div>
  </div>
  <div class="abs" style="left:209px;top:90px;width:1px;height:63px;background:#222"></div>
  <div class="abs" style="left:164px;top:35px;width:91px;height:91px;border-radius:50%;background:#111"></div>
  <div class="photo ph-red" role="img" aria-label="Colourful fibre light inside a circle" style="left:164px;top:40px;width:80px;height:80px;border-radius:50%"></div>
  <div class="mark" style="left:179px;top:55px;width:50px;height:50px;background:#dfe3e8;font-size:5.5px">VeraMosk</div>
  <div class="foot">© 2023 VeraMosk group all rights reserved</div>
  <div class="pnum"></div>
</section>

<!-- Row 4 -->
<section class="slide" style="left:22px;top:616px">
  <div class="photo ph-red" role="img" aria-label="Red and blue fibre optic light" style="left:0;top:0;width:81px;height:153px"></div>
  <div class="brand" style="left:100px">Copper Thread</div>
  <div class="abs" style="left:221px;top:0;width:1px;height:153px;background:#ccc"></div>
  <div class="icon" style="left:208px;top:20px;width:27px;height:27px"><svg><use href="#i-server"/></svg></div>
  <div class="icon" style="left:208px;top:63px;width:27px;height:27px;background:var(--blue)"><svg><use href="#i-cloud"/></svg></div>
  <div class="icon" style="left:208px;top:106px;width:27px;height:27px;background:var(--blue)"><svg><use href="#i-net"/></svg></div>
  <div class="item abs" style="left:100px;top:25px;width:100px;text-align:right"><div class="h">Your Subtitle Slide Right Here</div><div class="p r">Lorem Ipsum is simply dummy text of the printing and typesetting industry. Lorem Ipsum has been the industry's standard dummy text ever since the 1500s</div></div>
  <div class="item abs" style="left:100px;top:68px;width:100px;text-align:right"><div class="h">Your Subtitle Slide Right Here</div><div class="p r">Lorem Ipsum is simply dummy text of the printing and typesetting industry. Lorem Ipsum has been the industry's standard dummy text ever since the 1500s</div></div>
  <div class="item abs" style="left:100px;top:111px;width:100px;text-align:right"><div class="h">Your Subtitle Slide Right Here</div><div class="p r">Lorem Ipsum is simply dummy text of the printing and typesetting industry. Lorem Ipsum has been the industry's standard dummy text ever since the 1500s</div></div>
  <div class="foot" style="left:40px">© 2023 VeraMosk group all rights reserved</div>
  <div class="pnum"></div>
</section>

<section class="slide" style="left:317px;top:616px">
  <div class="photo ph-fiber" role="img" aria-label="Bundle of blue fibre optic strands" style="left:0;top:0;width:107px;height:153px"></div>
  <div class="brand right">Copper Thread</div>
  <div class="abs" style="left:123px;top:22px;width:136px">
    <div class="title"><b>Your Title Slide</b><br>Goes Right Here</div>
    <div class="p" style="margin-top:4px">Lorem Ipsum is simply dummy text of the printing and typesetting industry. Lorem Ipsum has been the industry's standard dummy text ever since the 1500s, when an unknown printer took a galley of type and scrambled it to make a type specimen book. It has survived not only five centuries, but</div>
  </div>
  <div class="abs" style="left:44px;top:92px;width:132px;height:42px;background:#fff;box-shadow:0 1px 4px rgba(0,0,0,.2);padding:7px 6px;text-align:center;font-size:5.2px;line-height:6.4px;color:#222">
    <span style="position:absolute;left:4px;top:2px;font-size:14px;color:var(--sky);font-weight:900">“</span><b>Lorem Ipsum is simply</b> dummy text of the printing <b>and typesetting industry. Lorem Ipsum</b> has been the industry's <b>standard dummy text ever since the 1500s, when an</b>
  </div>
  <div class="item abs" style="left:190px;top:92px;width:70px"><div class="h">Your Subtitle Slide Right Here</div><div class="p" style="text-align:left">Lorem Ipsum is simply dummy text of the printing and typesetting industry.</div></div>
  <div class="item abs" style="left:190px;top:116px;width:70px"><div class="h">Your Subtitle Slide Right Here</div><div class="p" style="text-align:left">Lorem Ipsum is simply dummy text of the printing and typesetting industry.</div></div>
  <div class="foot" style="left:50px">© 2023 VeraMosk group all rights reserved</div>
  <div class="pnum"></div>
</section>

<section class="slide" style="left:612px;top:616px">
  <div class="brand">VeraMosk</div><div class="brand right">Copper Thread</div>
  <div class="abs" style="left:12px;top:30px;width:128px">
    <div class="title"><b>Your Title</b> Slide</div>
    <div class="dots"><i></i><i></i><i></i></div>
    <div class="sub">Your Subtitle Slide Goes Right Here</div>
    <div class="p">Lorem Ipsum is simply dummy text of the printing and typesetting industry. Lorem Ipsum has been the industry's standard dummy text ever since the 1500s, when an unknown printer took a galley of type and scrambled it to make a type specimen book. It has survived not only five centuries, but also the leap into electronic typesetting, remaining essentially unchanged. It was popularized in the 1960s with the release of</div>
  </div>
  <div class="abs" style="left:151px;top:36px;width:57px;height:81px;background:var(--sky);color:#fff;text-align:center;padding-top:6px">
    <svg width="9" height="9"><use href="#i-server"/></svg>
    <div style="font-size:7px;font-weight:500">12.5K</div><div style="font-size:2.8px;font-weight:700">Description</div>
    <svg width="9" height="9" style="margin-top:6px"><use href="#i-usb"/></svg>
    <div style="font-size:7px;font-weight:500">9.5K</div><div style="font-size:2.8px;font-weight:700">Description</div>
  </div>
  <div class="photo ph-fiber" role="img" aria-label="Blue fibre optic strands" style="left:210px;top:36px;width:61px;height:81px"></div>
  <div class="p c" style="position:absolute;left:12px;top:124px;width:253px">Lorem Ipsum is simply dummy text of the printing and typesetting industry. Lorem Ipsum has been the industry's standard dummy text ever since the 1500s, when an unknown printer took a galley of type and scrambled it to make a type specimen book. It has survived not only five</div>
  <div class="foot">© 2023 VeraMosk group all rights reserved</div>
  <div class="pnum"></div>
</section>

<section class="slide" style="left:906px;top:616px">
  <div class="brand">VeraMosk</div><div class="brand right">Copper Thread</div>
  <div class="abs" style="left:0;top:22px;width:271px;text-align:center"><div class="title"><b>Six Bullet</b> Title Slide</div></div>
  <div class="icon" style="left:24px;top:47px;width:19px;height:19px"><svg><use href="#i-usb"/></svg></div>
  <div class="item abs" style="left:50px;top:46px;width:75px"><div class="h">Your Subtitle Slide Right Here</div><div class="p">Lorem Ipsum is simply dummy text of the printing and typesetting industry. Lorem Ipsum has been the industry's</div></div>
  <div class="icon" style="left:24px;top:81px;width:19px;height:19px;background:var(--blue)"><svg><use href="#i-monitor"/></svg></div>
  <div class="item abs" style="left:50px;top:80px;width:75px"><div class="h">Your Subtitle Slide Right Here</div><div class="p">Lorem Ipsum is simply dummy text of the printing and typesetting industry. Lorem Ipsum has been the industry's</div></div>
  <div class="icon" style="left:24px;top:116px;width:19px;height:19px;background:var(--blue)"><svg><use href="#i-plug"/></svg></div>
  <div class="item abs" style="left:50px;top:115px;width:75px"><div class="h">Your Subtitle Slide Right Here</div><div class="p">Lorem Ipsum is simply dummy text of the printing and typesetting industry. Lorem Ipsum has been the industry's</div></div>
  <div class="icon" style="left:149px;top:47px;width:19px;height:19px;background:var(--blue)"><svg><use href="#i-server"/></svg></div>
  <div class="item abs" style="left:175px;top:46px;width:75px"><div class="h">Your Subtitle Slide Right Here</div><div class="p">Lorem Ipsum is simply dummy text of the printing and typesetting industry. Lorem Ipsum has been the industry's</div></div>
  <div class="icon" style="left:149px;top:81px;width:19px;height:19px;background:var(--blue)"><svg><use href="#i-cloud"/></svg></div>
  <div class="item abs" style="left:175px;top:80px;width:75px"><div class="h">Your Subtitle Slide Right Here</div><div class="p">Lorem Ipsum is simply dummy text of the printing and typesetting industry. Lorem Ipsum has been the industry's</div></div>
  <div class="icon" style="left:149px;top:116px;width:19px;height:19px"><svg><use href="#i-net"/></svg></div>
  <div class="item abs" style="left:175px;top:115px;width:75px"><div class="h">Your Subtitle Slide Right Here</div><div class="p">Lorem Ipsum is simply dummy text of the printing and typesetting industry. Lorem Ipsum has been the industry's</div></div>
  <div class="foot">© 2023 VeraMosk group all rights reserved</div>
  <div class="pnum"></div>
</section>

<!-- Row 5 -->
<section class="slide" style="left:22px;top:801px;background:linear-gradient(135deg,#1f2f95,#1a2a7e)">
  <div class="brand light">VeraMosk</div><div class="brand right light">Copper Thread</div>
  <div class="abs" style="left:20px;top:26px;width:118px">
    <div class="title light"><b>Your Title Slide</b><br>Goes Right Here</div>
    <div class="p light-text" style="margin-top:4px;font-weight:700;font-size:3.4px">Lorem Ipsum is simply dummy text of the printing and typesetting industry. Lorem Ipsum has been the industry's</div>
    <div class="p light-text" style="margin-top:2px">Lorem Ipsum is simply dummy text of the printing and typesetting industry. Lorem Ipsum has been the industry's standard dummy text ever since the 1500s, when an unknown printer took a galley of type and scrambled it to make a type specimen book. It has survived not only five centuries, but also the leap into electronic typesetting, remaining essentially</div>
  </div>
  <div class="photo ph-fiber" role="img" aria-label="Fibre optic light inside a circle" style="left:154px;top:26px;width:100px;height:100px;border-radius:50%"></div>
  <div class="mark" style="left:180px;top:52px;width:48px;height:48px;background:rgba(255,255,255,.85);font-size:5.5px">VeraMosk</div>
  <div class="foot" style="color:#cdd">© 2023 VeraMosk group all rights reserved</div>
  <div class="pnum"></div>
</section>

<section class="slide" style="left:317px;top:801px">
  <div class="brand">VeraMosk</div><div class="brand right">Copper Thread</div>
  <div class="photo ph-server" role="img" aria-label="Facility one server room" style="left:9px;top:22px;width:62px;height:53px"></div>
  <div class="abs" style="left:9px;top:69px;width:62px;height:6px;background:var(--navy);color:#fff;font-size:3px;text-align:center;line-height:6px;font-weight:700">Facility One</div>
  <div class="photo ph-server" role="img" aria-label="Facility two server room" style="left:74px;top:22px;width:62px;height:53px"></div>
  <div class="abs" style="left:74px;top:69px;width:62px;height:6px;background:var(--blue);color:#fff;font-size:3px;text-align:center;line-height:6px;font-weight:700">Facility Two</div>
  <div class="photo ph-server" role="img" aria-label="Facility three cable patch panel" style="left:9px;top:78px;width:127px;height:53px"></div>
  <div class="abs" style="left:129px;top:78px;width:7px;height:53px;background:var(--blue);color:#fff;font-size:3px;writing-mode:vertical-rl;transform:rotate(180deg);text-align:center;font-weight:700">Facility Three</div>
  <div class="abs" style="right:12px;top:30px;width:112px;text-align:right">
    <div class="title" style="text-align:right"><b>Your Title Slide</b><br>Goes Right Here</div>
    <div class="p r" style="margin-top:4px;color:#333;font-weight:700;font-size:3.4px">Lorem Ipsum is simply dummy text of the printing and typesetting industry. Lorem Ipsum has been</div>
    <div class="p r" style="margin-top:2px">Lorem Ipsum is simply dummy text of the printing and typesetting industry. Lorem Ipsum has been the industry's standard dummy text ever since the 1500s, when an unknown printer took a galley of type and scrambled it to make a type specimen book. It has survived not only five centuries, but also the leap into electronic typesetting, remaining essentially</div>
  </div>
  <div class="foot" style="left:40px">© 2023 VeraMosk group all rights reserved</div>
  <div class="pnum"></div>
</section>

<section class="slide" style="left:612px;top:801px">
  <div class="brand">VeraMosk</div><div class="brand right">Copper Thread</div>
  <div class="abs" style="left:0;top:22px;width:271px;text-align:center">
    <div class="title"><b>Team</b> Title Slide</div>
    <div class="p c" style="padding:2px 20px 0">Lorem Ipsum is simply dummy text of the printing and typesetting industry. Lorem Ipsum has been the industry's standard</div>
  </div>
  <div class="abs" style="left:37px;top:73px;width:8px;height:8px;border-radius:50%;background:var(--navy)"></div>
  <div class="abs" style="left:226px;top:73px;width:8px;height:8px;border-radius:50%;background:var(--blue)"></div>
  <div class="photo ph-server" role="img" aria-label="Team member portrait" style="left:61px;top:58px;width:37px;height:37px;border-radius:50%"></div>
  <div class="photo ph-server" role="img" aria-label="Team member portrait" style="left:113px;top:54px;width:45px;height:45px;border-radius:50%"></div>
  <div class="photo ph-server" role="img" aria-label="Team member portrait" style="left:173px;top:58px;width:37px;height:37px;border-radius:50%"></div>
  <div class="item abs" style="left:54px;top:105px;width:52px;text-align:center"><div class="h">Your Name Here</div><div class="p c" style="margin-top:2px">suscipit eros iste metus auctor id dapibus quam aliquam sied</div></div>
  <div class="item abs" style="left:110px;top:105px;width:52px;text-align:center"><div class="h">Your Name Here</div><div class="p c" style="margin-top:2px">suscipit eros iste metus auctor id dapibus quam aliquam sied</div></div>
  <div class="item abs" style="left:166px;top:105px;width:52px;text-align:center"><div class="h">Your Name Here</div><div class="p c" style="margin-top:2px">suscipit eros iste metus auctor id dapibus quam aliquam sied</div></div>
  <div class="foot">© 2023 VeraMosk group all rights reserved</div>
  <div class="pnum"></div>
</section>

<section class="slide" style="left:906px;top:801px">
  <div class="brand">VeraMosk</div><div class="brand right">Copper Thread</div>
  <div class="abs" style="left:12px;top:30px;width:118px">
    <div class="title"><b>Your Title</b> Slide</div>
    <div class="dots"><i></i><i></i><i></i></div>
    <div class="sub">Your Subtitle Slide Goes Right Here</div>
    <div class="p">Lorem Ipsum is simply dummy text of the printing and typesetting industry. Lorem Ipsum has been the industry's standard dummy text ever since the 1500s, when an unknown printer took a galley of type and scrambled it to make a type specimen book. It has survived not only five centuries, but also the leap into electronic typesetting, remaining essentially unchanged. It was popularized in the 1960s with the release of</div>
  </div>
  <div class="photo ph-server" role="img" aria-label="Server racks in a data hall" style="left:147px;top:45px;width:27px;height:43px"></div>
  <div class="photo ph-server" role="img" aria-label="Engineer at a server rack" style="left:196px;top:29px;width:52px;height:48px"></div>
  <div class="photo ph-keys" role="img" aria-label="Colleagues reviewing a tablet" style="left:176px;top:45px;width:18px;height:43px"></div>
  <div class="abs" style="left:160px;top:93px;width:33px;height:31px;background:var(--sky);display:flex;align-items:center;justify-content:center"><svg width="12" height="12"><use href="#i-usb"/></svg></div>
  <div class="photo ph-server" role="img" aria-label="Technician connecting cables" style="left:196px;top:81px;width:45px;height:43px"></div>
  <div class="foot">© 2023 VeraMosk group all rights reserved</div>
  <div class="pnum"></div>
</section>

<!-- Row 6 -->
<section class="slide" style="left:22px;top:986px">
  <div class="brand">VeraMosk</div><div class="brand right">Copper Thread</div>
  <div class="abs" style="left:0;top:22px;width:271px;text-align:center">
    <div class="title"><b>Your Title</b> Slide</div>
    <div class="p c" style="padding:3px 14px 0">Lorem Ipsum is simply dummy text of the printing and typesetting industry. Lorem Ipsum has been the industry's standard dummy text ever since the 1500s, when an unknown printer took a galley of type and scrambled it to make a type specimen book. It has survived not only five centuries, but also the leap into electronic typesetting, remaining essentially unchanged. It was popularized in the 1960s with the release of the</div>
  </div>
  <div class="abs" style="left:10px;top:73px;display:grid;grid-template-columns:repeat(7,34px);grid-auto-rows:31px;gap:2px">
    <div style="background:var(--navy);display:flex;align-items:center;justify-content:center"><svg width="10" height="10"><use href="#i-monitor"/></svg></div>
    <div class="ph-server" role="img" aria-label="Server rack"></div>
    <div class="ph-keys" role="img" aria-label="Office team"></div>
    <div class="ph-fiber" role="img" aria-label="Fibre cable bundle"></div>
    <div class="ph-server" role="img" aria-label="Engineer at work"></div>
    <div class="ph-fiber" role="img" aria-label="Blue light strands"></div>
    <div style="background:var(--sky);display:flex;align-items:center;justify-content:center"><svg width="10" height="10"><use href="#i-server"/></svg></div>
    <div class="ph-purple" role="img" aria-label="Purple fibre light"></div>
    <div class="ph-server" role="img" aria-label="Cable patching"></div>
    <div class="ph-fiber" role="img" aria-label="Fibre ends"></div>
    <div style="background:var(--blue);display:flex;align-items:center;justify-content:center"><svg width="10" height="10"><use href="#i-plug"/></svg></div>
    <div class="ph-purple" role="img" aria-label="Glowing strands"></div>
    <div class="ph-server" role="img" aria-label="Engineer in server room"></div>
    <div class="ph-purple" role="img" aria-label="Violet fibre light"></div>
  </div>
  <div class="foot">© 2023 VeraMosk group all rights reserved</div>
  <div class="pnum"></div>
</section>

<section class="slide" style="left:317px;top:986px;background:linear-gradient(135deg,#2a9ee0,#1e7fd0)">
  <div class="brand light">VeraMosk</div><div class="brand right light">Copper Thread</div>
  <div class="abs" style="left:19px;top:30px;width:98px;height:98px;border-radius:50%;background:linear-gradient(135deg,#5c2aa8,#1d2d8a)"></div>
  <div class="mark" style="left:28px;top:38px;width:82px;height:82px;font-size:8px">VeraMosk</div>
  <div class="abs" style="right:12px;top:30px;width:124px;text-align:right">
    <div class="title light" style="text-align:right"><b>Your Title Slide</b><br>Goes Right Here</div>
    <div class="p r light-text" style="margin-top:4px;font-weight:700;font-size:3.4px">Lorem Ipsum is simply dummy text of the printing and typesetting industry. Lorem Ipsum has been the industry's</div>
    <div class="p r light-text" style="margin-top:2px">Lorem Ipsum is simply dummy text of the printing and typesetting industry. Lorem Ipsum has been the industry's standard dummy text ever since the 1500s, when an unknown printer took a galley of type and scrambled it to make a type specimen book. It has survived not only five centuries, but also the leap into electronic typesetting, remaining essentially</div>
  </div>
  <div class="foot" style="color:#def">© 2023 VeraMosk group all rights reserved</div>
  <div class="pnum"></div>
</section>

<section class="slide" style="left:612px;top:986px">
  <div class="photo ph-purple" role="img" aria-label="Red and purple fibre optic light" style="left:0;top:0;width:271px;height:64px"></div>
  <div class="brand light">VeraMosk</div><div class="brand right light">Copper Thread</div>
  <div class="abs" style="left:10px;top:78px;width:115px">
    <div class="title"><b>Your Title</b> Slide</div>
    <div class="dots"><i></i><i></i><i></i></div>
    <div class="p">Lorem Ipsum is simply dummy text of the printing and typesetting industry. Lorem Ipsum has been the industry's standard dummy text ever since the 1500s, when an unknown printer took a galley of type and scrambled it to</div>
  </div>
  <div class="icon" style="left:133px;top:50px;width:30px;height:30px"><svg><use href="#i-server"/></svg></div>
  <div class="icon" style="left:176px;top:50px;width:30px;height:30px;background:var(--blue)"><svg><use href="#i-plug"/></svg></div>
  <div class="icon" style="left:219px;top:50px;width:30px;height:30px;background:var(--sky)"><svg><use href="#i-monitor"/></svg></div>
  <div class="item abs" style="left:131px;top:91px;width:37px"><div class="h" style="text-align:center">Your Subtitle Slide</div><div class="p">Lorem Ipsum is simply dummy text of the printing and typesetting industry. Lorem Ipsum has been the industry's</div></div>
  <div class="item abs" style="left:174px;top:91px;width:37px"><div class="h" style="text-align:center">Your Subtitle Slide</div><div class="p">Lorem Ipsum is simply dummy text of the printing and typesetting industry. Lorem Ipsum has been the industry's</div></div>
  <div class="item abs" style="left:217px;top:91px;width:37px"><div class="h" style="text-align:center">Your Subtitle Slide</div><div class="p">Lorem Ipsum is simply dummy text of the printing and typesetting industry. Lorem Ipsum has been the industry's</div></div>
  <div class="foot">© 2023 VeraMosk group all rights reserved</div>
  <div class="pnum"></div>
</section>

<section class="slide" style="left:906px;top:986px">
  <div class="abs" style="left:193px;top:0;width:78px;height:153px;background:linear-gradient(180deg,#2a8ee0,#1d2d8a 55%,#15206a)"></div>
  <div class="brand">VeraMosk</div><div class="brand right light">Copper Thread</div>
  <div class="abs" style="left:12px;top:30px;width:118px">
    <div class="title"><b>Your Title</b> Slide</div>
    <div class="dots"><i></i><i></i><i></i></div>
    <div class="sub">Your Subtitle Slide Goes Right Here</div>
    <div class="p">Lorem Ipsum is simply dummy text of the printing and typesetting industry. Lorem Ipsum has been the industry's standard dummy text ever since the 1500s, when an unknown printer took a galley of type and scrambled it to make a type specimen book. It has survived not only five centuries, but also the leap into electronic typesetting, remaining essentially unchanged. It was popularized in the 1960s with the release of</div>
  </div>
  <div class="abs" style="left:140px;top:38px;width:94px;height:70px;background:#222;border-radius:3px;padding:3px">
    <div class="ph-server" role="img" aria-label="Engineer at a server rack shown on a laptop screen" style="width:100%;height:100%"></div>
  </div>
  <div class="abs" style="left:134px;top:108px;width:106px;height:4px;background:#cfd2d6;border-radius:0 0 3px 3px"></div>
  <div class="foot">© 2023 VeraMosk group all rights reserved</div>
  <div class="pnum"></div>
</section>
</body>
</html>
```